Business Card Design Project

I need a business card designed from scratch. I have an existing logo that I can upload in Illustrator for modification or redesign.

The Company is called Query Lanterns http://querylanterns.com.au and we provide Search Engine Optimization services to Australian businesses. The current logo signifies an increase in visitors, profits etc...

There are no restrictions as to the redesign - colours, style etc are all open to change.

Cards will be full colour and one sided printed at http://www.cardmoxel.com.au so check their requirements for file format and sizes etc.

I will expect all original files upon completion of project.

Target Market(s)

Any business with a web site looking to improve their search engine rankings

Industry/Entity Type

Business

Requirements
Must have
• I like modern, sleek designs. Clean, not fussy, uncluttered.

```html
<!DOCTYPE html>
<html lang="en">
<head>
<meta charset="utf-8">
<title>Query Lanterns – Business Card</title>
<link href="https://fonts.googleapis.com/css2?family=Open+Sans:wght@400;600;700&display=swap" rel="stylesheet">
<style>
  :root {
    --backdrop: #e6e2dd;
    --card: #ffffff;
    --brand-blue: #1c6fb5;
    --band-dark: #17365f;
    --band-light: #2a86c8;
    --rule: #2b2b2b;
    --ink: #3a3a3a;
    --on-band: #ffffff;
  }
  * { margin: 0; padding: 0; box-sizing: border-box; }
  html, body {
    width: 1200px; height: 412px; overflow: hidden;
    background: var(--backdrop);
    font-family: "Open Sans", Arial, sans-serif;
  }
  .canvas { position: relative; width: 1200px; height: 412px; }
  .card {
    position: absolute; top: 65px;
    width: 497px; height: 283px;
    background: var(--card);
    box-shadow: 0 2px 8px rgba(0,0,0,0.25);
    overflow: hidden;
  }
  .card--front { left: 73px; }
  .card--back { left: 631px; }

  .brand {
    position: absolute; left: 36px; top: 36px;
    display: flex; align-items: center; gap: 10px;
  }
  .brand__dot {
    width: 22px; height: 22px; border-radius: 50%;
    background: var(--brand-blue);
  }
  .brand__name {
    font-weight: 700; font-size: 27px; color: var(--brand-blue);
    letter-spacing: -0.3px;
  }

  .contact {
    position: absolute; left: 36px; top: 115px;
    list-style: none; font-size: 12.5px; color: var(--ink);
  }
  .contact li { display: flex; align-items: center; gap: 6px; height: 16.5px; }
  .contact svg { width: 10px; height: 10px; fill: var(--ink); flex: none; }

  .band-rule {
    position: absolute; left: 0; right: 0; height: 1.5px;
    background: var(--rule);
  }
  .band-rule--top { top: 182px; }
  .band-rule--bottom { top: 222px; }
  .band {
    position: absolute; left: 0; right: 0; top: 186px; height: 33px;
    background: linear-gradient(90deg, var(--band-dark) 0%, var(--band-dark) 25%, var(--band-light) 100%);
    display: flex; align-items: center; padding-left: 36px;
    color: var(--on-band);
  }
  .band__name { font-weight: 700; font-size: 15px; }
  .band__title { font-size: 13px; margin-left: 4px; }
  .band__url { font-weight: 600; font-size: 12.5px; padding-left: 17px; }

  .address {
    position: absolute; left: 36px; top: 251px;
    font-style: normal; font-size: 12.5px; line-height: 17px; color: var(--ink);
  }
</style>
</head>
<body>
<main class="canvas">
  <section class="card card--front" aria-label="Card front">
    <div class="brand">
      <span class="brand__dot"></span>
      <span class="brand__name">Query Lanterns</span>
    </div>

    <ul class="contact">
      <li><svg viewBox="0 0 10 10"><path d="M2 0h2l1 3-1.5 1a6 6 0 0 0 2.5 2.5L7 5l3 1v2c0 1-1 2-2 2C4 10 0 6 0 2c0-1 1-2 2-2z"/></svg>098 765 4321</li>
      <li><svg viewBox="0 0 10 10"><rect x="2.5" y="0" width="5" height="10" rx="1"/></svg>098 765 4321</li>
      <li><svg viewBox="0 0 10 10"><path d="M0 2h10v6H0z M0 2l5 3.5L10 2" /></svg>enquiry@querylanterns.com.au</li>
      <li><svg viewBox="0 0 10 10"><circle cx="5" cy="5" r="5"/></svg>www.querylanterns.com.au</li>
    </ul>

    <div class="band-rule band-rule--top"></div>
    <div class="band">
      <span class="band__name">Your Name /</span><span class="band__title">Title</span>
    </div>
    <div class="band-rule band-rule--bottom"></div>

    <address class="address">Complex name,Street name<br>City, State, zip code</address>
  </section>

  <section class="card card--back" aria-label="Card back">
    <div class="band-rule band-rule--top"></div>
    <div class="band">
      <span class="band__url">www.querylanterns.com.au</span>
    </div>
    <div class="band-rule band-rule--bottom"></div>
  </section>
</main>
</body>
</html>
```